Brintel Works - Fast, Efficient and Gas Mainteance for Domestic, Commercial and Industrial clients

We are in the process of purchasing a new business and would like to get a new logo and business card.
Business is a gas maintenance business that also does new gas installations.
Has been established since 1988.
Services include:
Install all types of gas appliances & equipment inc. hot water units
Maintain / repair / replace all types of gas appliances & equipment

Target Market(s)

Domestic, Commercial and Industrial clients

Industry/Entity Type

Business

Contact Information for Business Card

admin@brintelworks.com.au
07 3918 4726
Brintel Works PTY LTD

Logo Text

Gas Fitting & Plumbing Maintenance Specialists

Font styles to use
Sans Serif

Requirements
Must have
• Logo
• Business name, contact number, email address, web address
• Domestic | Commercial | Industrial Est Since 1988
Nice to have
• Possibly a black card with a flame logo to one side
Should not have
• Spelling errors

```html
<!DOCTYPE html>
<html lang="en">
<head>
<meta charset="utf-8">
<title>Brintel Works – Business Card</title>
<link rel="stylesheet" href="https://fonts.googleapis.com/css2?family=Open+Sans:wght@400;600;700&family=Roboto:wght@400&family=Dancing+Script&display=swap">
<style>
  :root {
    --stage: #e4e1dc;
    --card-white: #ffffff;
    --accent: #e8765a;
    --ink: #58606a;
    --ink-soft: #9aa0a6;
    --ink-dark: #2b2b2b;
    --mark-faint: #e3e3e4;
    --card-black: #0d0d0d;
    --on-black: #f2f2f2;
  }
  * { margin: 0; padding: 0; box-sizing: border-box; }
  html, body { width: 1200px; height: 892px; overflow: hidden; }
  body {
    background: var(--stage);
    position: relative;
    font-family: "Open Sans", sans-serif;
  }
  .card {
    position: absolute;
    left: 250px;
    width: 700px;
    height: 400px;
    overflow: hidden;
    box-shadow: 0 6px 18px rgba(0,0,0,.18);
  }
  .card--front { top: 30px; background: var(--card-white); }
  .card--back  { top: 462px; background: var(--card-black); }

  .card__swoosh { position: absolute; inset: 0; }

  .brand-mark {
    position: absolute; left: 30px; top: 118px;
    width: 56px; height: 56px; border-radius: 50%;
    background: var(--mark-faint);
  }

  .brand { position: absolute; left: 100px; top: 48px; }
  .brand__name {
    font-size: 44px; font-weight: 600; color: var(--accent);
    letter-spacing: 1px; line-height: 1;
  }
  .brand__suffix {
    font-size: 10px; font-weight: 600; color: var(--ink);
    vertical-align: top; margin-left: 4px; letter-spacing: .5px;
  }
  .brand__tagline {
    margin-top: 8px; font-size: 23px; font-weight: 700; color: var(--ink);
  }
  .brand__sectors {
    margin-top: 4px; font-size: 13px; color: var(--ink-soft);
    display: flex; align-items: baseline; gap: 14px;
  }
  .brand__est {
    font-family: "Dancing Script", cursive; font-size: 23px; color: var(--ink-soft);
  }

  .contact {
    position: absolute; left: 404px; top: 264px;
    list-style: none; font-family: "Roboto", sans-serif;
    font-size: 17px; color: var(--ink-dark);
  }
  .contact__item { display: flex; align-items: center; gap: 12px; height: 25px; }
  .contact__icon { width: 15px; height: 15px; flex: none; }

  .back-text {
    position: absolute; left: 0; right: 0; top: 120px; text-align: center;
  }
  .back-text__name {
    font-size: 40px; font-weight: 600; color: var(--accent); letter-spacing: .5px;
  }
  .back-text__tagline {
    margin-top: 14px; font-size: 22px; color: var(--on-black);
  }
  .back-text__sectors {
    margin-top: 10px; font-size: 20px; color: var(--on-black);
  }
  .card__gloss {
    position: absolute; inset: 0;
    background: linear-gradient(120deg, rgba(255,255,255,.10) 0%, rgba(255,255,255,0) 40%);
  }
</style>
</head>
<body>

<section class="card card--front" aria-label="Business card front">
  <svg class="card__swoosh" viewBox="0 0 700 400" width="700" height="400" aria-hidden="true">
    <defs>
      <linearGradient id="shade" x1="0" y1="0" x2="1" y2="1">
        <stop offset="0" stop-color="#f6f6f6"/>
        <stop offset="1" stop-color="#e2e2e3"/>
      </linearGradient>
    </defs>
    <path d="M0 0 H700 V10 C660 140 560 215 380 235 C220 262 90 300 0 370 Z" fill="url(#shade)"/>
    <path d="M700 10 C660 140 560 215 380 235 C220 262 90 300 0 370" fill="none" stroke="#ffffff" stroke-width="12"/>
    <path d="M716 10 C676 148 576 229 396 250 C236 276 100 312 0 386" fill="none" stroke="var(--accent)" stroke-width="8"/>
  </svg>

  <div class="brand-mark" aria-hidden="true"></div>

  <div class="brand">
    <div class="brand__name">BRINTEL WORKS<span class="brand__suffix">PTY LTD</span></div>
    <div class="brand__tagline">Gas fitting &amp; Plumbing Specialists</div>
    <div class="brand__sectors"><span>Domestic | Commercial | Industrial</span><span class="brand__est">Est Since 1988</span></div>
  </div>

  <ul class="contact">
    <li class="contact__item">
      <svg class="contact__icon" viewBox="0 0 16 16"><rect width="16" height="16" rx="2" fill="var(--accent)"/><path d="M5 4c-1 1-1 3 1 5s4 2 5 1l-1.5-1.5-1.2.8C7.5 8.7 7.3 8.5 6.7 7.7l.8-1.2z" fill="#fff"/></svg>
      <span>07 3918 4726</span>
    </li>
    <li class="contact__item">
      <svg class="contact__icon" viewBox="0 0 16 16"><rect width="16" height="16" rx="2" fill="var(--accent)"/><rect x="4" y="6" width="8" height="6" fill="#fff"/><rect x="5.5" y="3.5" width="5" height="3" fill="none" stroke="#fff"/></svg>
      <span>07 3918 4739</span>
    </li>
    <li class="contact__item">
      <svg class="contact__icon" viewBox="0 0 16 16"><rect width="16" height="16" rx="2" fill="var(--accent)"/><circle cx="8" cy="8" r="4.5" fill="none" stroke="#fff"/><path d="M3.5 8h9M8 3.5c-2 3-2 6 0 9M8 3.5c2 3 2 6 0 9" fill="none" stroke="#fff" stroke-width=".8"/></svg>
      <span>www.brintelworks.com.au</span>
    </li>
    <li class="contact__item">
      <svg class="contact__icon" viewBox="0 0 16 16"><rect width="16" height="16" rx="2" fill="var(--accent)"/><rect x="3.5" y="5" width="9" height="6.5" fill="#fff"/><path d="M3.5 5l4.5 3.5L12.5 5" fill="none" stroke="var(--accent)"/></svg>
      <span>admin@brintelworks.com.au</span>
    </li>
    <li class="contact__item">
      <svg class="contact__icon" viewBox="0 0 16 16"><rect width="16" height="16" rx="2" fill="var(--accent)"/><path d="M8 13s-3.5-4-3.5-6a3.5 3.5 0 0 1 7 0c0 2-3.5 6-3.5 6z" fill="#fff"/><circle cx="8" cy="7" r="1.2" fill="var(--accent)"/></svg>
      <span>PO Box 2864, Ashgrove, QLD 4060</span>
    </li>
  </ul>
</section>

<section class="card card--back" aria-label="Business card back">
  <div class="back-text">
    <div class="back-text__name">Brintel Works PTY LTD</div>
    <div class="back-text__tagline">Gas fitting &amp; Plumbing Specialists</div>
    <div class="back-text__sectors">Domestic | Commercial | Industrial Est Since 1988</div>
  </div>
  <div class="card__gloss"></div>
</section>

</body>
</html>
```